Coastal Learner Bureau business cards

Australian company about to start offering its services. We recruit international students to come to study English, vocational education and postgraduate courses in Australia. We help them find the institution and select the right city they want to come to Australia. We are a young, online oriented and supportive agency. Our clients are between 18 and 35 years old, mainly University students, young professionals or people with work experience. We provide much more information that any other agency offer. We administrate a Facebook group with more than 11.000 members that daily ask questions about general information when coming to Australia, while they are here and even after they leave the country

Target Market(s)

International students from South America, Central America and Europe

Industry/Entity Type

Student

Contact Information for Business Card

Tomas Bilbrea
Managing Director
tomas@kelvarin.com.au
www.kelvoria.com.au
+61 491058264
Melbourne, Australia

Font styles to use
Serif
Sans Serif

Colors

Designer to choose colors to be used in the design.

Requirements
Must have
• Horizontal design
• Standard business card size and shape. If font uses green or yellow colours, they will have to match the ones from the logo
Nice to have
• UPDATE: Use the contents of the green image to design one of the card sides. Use our logo in the background of that side as watermark.
• Passport image, or immigration stamps. A picture of the Yarra River (from Melbourne) would be cool as well.
Should not have
• Non-standard business card size and shape
• Not black as the background colour of any sides as we are not a VIP agency or a hight class service. We are orientes to young people and they like colours, pictures, something attractive.
• Vertical design
• NO YELLOW or BLACK AS THE BACKGROUND COLOUR OF ANY SIDE OF THE BIZ CARD

```html
<!DOCTYPE html>
<html lang="en">
<head>
<meta charset="utf-8">
<title>Coastal Learner Bureau – Business Card</title>
<link rel="stylesheet" href="https://fonts.googleapis.com/css2?family=PT+Sans:wght@400;700&family=Tinos:wght@700&display=swap">
<style>
  :root {
    --brand-green: #136445;
    --brand-yellow: #e6bf17;
    --card-paper: #f5f3f2;
    --ink: #2a2a2a;
    --stage: #e4e2df;
    --white: #ffffff;
  }
  * { margin: 0; padding: 0; box-sizing: border-box; }
  html, body {
    width: 1200px; height: 900px; overflow: hidden;
    background: var(--stage);
  }
  .card {
    position: absolute;
    left: 150px; top: 174px;
    width: 900px; height: 552px;
    background: var(--card-paper);
    box-shadow: 0 6px 24px rgba(0,0,0,0.12);
    overflow: hidden;
    font-family: "PT Sans", Arial, sans-serif;
  }
  .card__panel { position: absolute; inset: 0; width: 900px; height: 552px; }
  .brand-name {
    position: absolute; left: 51px; top: 118px;
    font-size: 92px; font-weight: 700; line-height: 1;
    color: var(--brand-green);
    letter-spacing: -1px;
  }
  .tagline {
    position: absolute; left: 51px; top: 310px;
    font-family: "Tinos", "Times New Roman", serif;
    font-weight: 700; font-size: 27px;
    color: var(--brand-green);
  }
  .person { position: absolute; left: 49px; top: 424px; }
  .person__name {
    font-size: 29px; line-height: 1.1; text-transform: uppercase;
    color: var(--brand-yellow);
  }
  .person__surname { color: var(--brand-green); }
  .person__role { font-size: 23px; color: var(--ink); margin-top: 4px; }
  .contact {
    position: absolute; right: 45px; top: 308px;
    list-style: none; text-align: right;
    color: var(--white); font-size: 23px; line-height: 33px;
  }
  .contact li { display: flex; justify-content: flex-end; align-items: center; gap: 12px; }
  .contact svg { width: 18px; height: 18px; flex: none; }
  .location {
    position: absolute; right: 48px; top: 466px;
    color: var(--white); font-size: 24px;
  }
</style>
</head>
<body>
  <div class="card">
    <svg class="card__panel" viewBox="0 0 900 552" aria-hidden="true">
      <path d="M590,-4 C540,150 515,330 548,556 L904,556 L904,-4 Z"
            fill="var(--brand-green)" stroke="var(--brand-yellow)" stroke-width="4"/>
    </svg>

    <div class="brand-name">Kelvoria</div>
    <p class="tagline">HACEMOS MÁS POR TI!</p>

    <div class="person">
      <p class="person__name">Tomas <span class="person__surname">Bilbrea</span></p>
      <p class="person__role">Managing Director</p>
    </div>

    <ul class="contact">
      <li>+61 491058264
        <svg viewBox="0 0 24 24"><path fill="var(--brand-yellow)" d="M6.6 10.8a15 15 0 0 0 6.6 6.6l2.2-2.2c.3-.3.7-.4 1-.2 1.1.4 2.3.6 3.6.6.6 0 1 .4 1 1V20c0 .6-.4 1-1 1A17 17 0 0 1 3 4c0-.6.4-1 1-1h3.5c.6 0 1 .4 1 1 0 1.3.2 2.5.6 3.6.1.3 0 .7-.2 1z"/></svg>
      </li>
      <li>tomas@kelvarin.com.au
        <svg viewBox="0 0 24 24"><rect x="2" y="5" width="20" height="14" fill="var(--brand-yellow)"/><path d="M2 5l10 8 10-8" fill="none" stroke="var(--brand-green)" stroke-width="2"/></svg>
      </li>
      <li>www.kelvoria.com.au
        <svg viewBox="0 0 24 24"><circle cx="12" cy="12" r="10" fill="var(--brand-yellow)"/><path d="M2 12h20M12 2c3 3 3 17 0 20M12 2c-3 3-3 17 0 20" fill="none" stroke="var(--brand-green)" stroke-width="1.5"/></svg>
      </li>
    </ul>
    <p class="location">Melbourne, Australia</p>
  </div>
</body>
</html>
```